Roofing Company Modern look

I want a modern and sophisticated look for our roofing business.

Our address is :

5217 Mallow Creek Ln
Orlando, Fl 32825

(407)-583-2196

www.HarborlineRoofsFl.com

I also want to make sure on the back there is a spot to put
Project Manager Name :

Number:

Because the cards will be used by all sales people

Project Manager Name :

Also there are accreditation we have logos are uploaded here as well that I would like maybe on the back of card as well

I also want to highlight our special attributions or trades:

Residential & Commercial
Fully Insured
License # CCC7482913
Insurance Claims
Serving Central Florida Since 1992
Free Estimates

Contact Information for Business Card

Our address is :

5217 Mallow Creek Ln
Orlando, Fl 32825

(407)-583-2196

Project Manager Name :

Residential & Commercial
Fully Insured
License # CCC7482913
Insurance Claims
Free Estimates

Font styles to use
Serif
Sans Serif

Colors
3176b5

Requirements
Must have
• Must have royal blue like my logo grey and black are the colors I like

```html
<!DOCTYPE html>
<html lang="en">
<head>
<meta charset="utf-8">
<title>Harborline Roofs &amp; Gutters – Business Card</title>
<link rel="stylesheet" href="https://fonts.googleapis.com/css2?family=Open+Sans:wght@400;600;700&display=swap">
<style>
  :root{
    --royal:#1f6fc4;
    --royal-deep:#0d56bb;
    --sky:#1c93d8;
    --ink:#4a4a4a;
    --muted:#6b6b6b;
    --rule:#c9c9c9;
    --silver:#cfd3d8;
    --paper:#ffffff;
    --backdrop:#e8eaed;
  }
  *{margin:0;padding:0;box-sizing:border-box}
  html,body{width:1200px;height:1188px;overflow:hidden;background:var(--backdrop)}
  body{font-family:"Open Sans",Arial,sans-serif;position:relative}
  .card{position:absolute;left:150px;width:900px;height:514px;border-radius:22px;overflow:hidden;
        box-shadow:0 8px 22px rgba(0,0,0,.18)}
  .card--front{top:60px;background:var(--paper)}
  .card--back{top:614px;background:linear-gradient(100deg,var(--royal-deep) 0%,#1378cc 55%,var(--sky) 100%)}

  /* front */
  .brand{position:absolute;left:40px;top:120px;width:420px;text-align:center;color:var(--royal)}
  .brand__dot{display:block;width:86px;height:86px;margin:0 auto 20px;border-radius:50%;background:var(--royal)}
  .brand__name{font-weight:600;font-size:46px;letter-spacing:2px;line-height:1}
  .brand__sub{font-weight:600;font-size:21px;letter-spacing:3px;margin-top:8px;text-transform:uppercase}
  .divider{position:absolute;left:490px;top:110px;width:1px;height:238px;background:var(--rule)}
  .contact{position:absolute;left:535px;top:110px;color:var(--ink)}
  .contact__name{font-weight:700;font-size:32px;color:var(--royal);line-height:1.1;text-transform:uppercase}
  .contact__role{font-size:19px;margin-top:6px}
  .contact__address{font-size:19px;line-height:31px;margin-top:16px}
  .contact__list{list-style:none;margin-top:16px;font-size:19px;line-height:31px}
  .contact__list li{display:flex;align-items:center;gap:12px}
  .contact__list svg{width:17px;height:17px;fill:var(--royal);flex:none}
  .attributes{position:absolute;left:0;right:0;top:400px;text-align:center;color:var(--muted);font-size:19px;line-height:33px}
  .attributes .sep{color:var(--royal);margin:0 8px}

  /* back */
  .back-brand{position:absolute;left:0;right:0;top:120px;text-align:center;color:var(--silver)}
  .back-brand .brand__dot{background:var(--silver)}
  .swoosh{position:absolute;left:0;top:0;width:900px;height:514px}
  .badges{position:absolute;left:565px;top:448px;display:flex;align-items:center;gap:22px}
  .badge{background:#b9bfc6}
  .badge--wide{width:136px;height:38px;border-radius:4px;background:linear-gradient(90deg,#d8262b 0 26%,#2a3f7a 26%)}
  .badge--round{width:40px;height:40px;border-radius:50%}
  .badge--navy{background:#2e4a7d}
</style>
</head>
<body>

<section class="card card--front" aria-label="Business card front">
  <div class="brand">
    <span class="brand__dot"></span>
    <div class="brand__name">HARBORLINE</div>
    <div class="brand__sub">Roofs &amp; Gutters Inc.</div>
  </div>

  <div class="divider"></div>

  <div class="contact">
    <h1 class="contact__name">Dana Whitcomb</h1>
    <p class="contact__role">Project Manager</p>
    <p class="contact__address">5217 Mallow Creek Ln<br>Orlando, Fl 32825</p>
    <ul class="contact__list">
      <li><svg viewBox="0 0 24 24"><path d="M6.6 10.8a15.1 15.1 0 0 0 6.6 6.6l2.2-2.2c.3-.3.7-.4 1-.2 1.1.4 2.3.6 3.6.6.6 0 1 .4 1 1V20c0 .6-.4 1-1 1A17 17 0 0 1 3 4c0-.6.4-1 1-1h3.5c.6 0 1 .4 1 1 0 1.3.2 2.5.6 3.6.1.3 0 .7-.2 1z"/></svg>(407)-583-2196</li>
      <li><svg viewBox="0 0 24 24"><path d="M2 5h20v14H2zm2 2v.5l8 5 8-5V7zm0 2.8V17h16V9.8l-8 5z"/></svg>info@HarborlineRoofsFl.com</li>
      <li><svg viewBox="0 0 24 24"><circle cx="12" cy="12" r="10"/></svg>www.HarborlineRoofsFl.com</li>
    </ul>
  </div>

  <p class="attributes">
    Residential &amp; Commercial<span class="sep">|</span>Fully Insured<span class="sep">|</span>License # CCC7482913<br>
    Insurance Claims<span class="sep">|</span>Serving Central Florida Since 1992<span class="sep">|</span>Free Estimates
  </p>
</section>

<section class="card card--back" aria-label="Business card back">
  <div class="back-brand">
    <span class="brand__dot"></span>
    <div class="brand__name">HARBORLINE</div>
    <div class="brand__sub">Roofs &amp; Gutters Inc.</div>
  </div>

  <svg class="swoosh" viewBox="0 0 900 514" aria-hidden="true">
    <path d="M395 514 C 520 430, 640 400, 760 392 C 830 388, 875 370, 900 338 L900 514 Z" fill="#9aa3ad"/>
    <path d="M410 514 C 530 438, 648 410, 765 402 C 835 398, 878 380, 900 350 L900 514 Z" fill="#ffffff"/>
  </svg>

  <div class="badges">
    <span class="badge badge--wide"></span>
    <span class="badge badge--round"></span>
    <span class="badge badge--round badge--navy"></span>
    <span class="badge badge--round"></span>
  </div>
</section>

</body>
</html>
```